Larkhollow needs a Webpage Design

We need a webpage for Dr. XYZ who is doing consultancy practice in the area of speech, language, and reading disabilities. He is doing his consultancy practice as "Larkhollow Consultants". Our target market is clients with annual income of $100,000 or more in Chicago area. Our business philosophy is: "...We provide the best evidence-based services/interventions, at an affordable fee, and deal only with clients who seek such services...."

Dr. XYZ's area of research interests are: a) using assistive technology for communication for children with autism, b) early intervention with focus on parent participation, and c) language learning for children birth-to-five years.

He works at a public university whose school color is 'Orange". Home page should show two logos (university and practice). Each page should stand on its own and reflect the content with minimal scrolling. The colors should be subdued (not bright colors) to attract college educated wealthy individuals who are seeking best evidence-based practice in speech, language, and reading for their children.

We need five pages: Home, Consultation, Research, Professional Development, and Contact (with google map directions). The home page should have space for a picture and links for facebook, twitter, and google plus. Other pages should have space for at least one picture and links to pdf files.

The overall design should show healthcare service, evidence-based early intervention with focus on parent participation, and project that we are leaders in the field.

```html
<!DOCTYPE html>
<html lang="en">
<head>
<meta charset="utf-8">
<title>Larkhollow Consultants – Dr. XYZ</title>
<link rel="stylesheet" href="https://fonts.googleapis.com/css2?family=Oswald:wght@400;500&family=Open+Sans:wght@400;600&display=swap">
<style>
:root{
  --peach:#f8bb9b;
  --orange:#f3a079;
  --orange-text:#ef9a72;
  --blue:#93c2e2;
  --blue-band:#c4dff0;
  --tab:#b9d8ec;
  --tab-text:#3f5566;
  --header-bg:#ededed;
  --teal:#b7dad6;
  --ink:#4a4a4a;
  --ink-soft:#6b6b6b;
  --white:#ffffff;
}
*{box-sizing:border-box;margin:0;padding:0}
html,body{width:755px;height:1200px;overflow:hidden;background:var(--white)}
body{position:relative;font-family:"Open Sans",Arial,sans-serif;color:var(--ink);font-size:8px;line-height:1.4}
.abs{position:absolute}

/* top strip */
.top-strip{left:0;top:0;width:755px;height:11px;background:var(--peach)}
.search{left:565px;top:1px;width:78px;height:9px;background:var(--white);border:1px solid #d6d6d6;font-size:6px;color:#777;padding-left:3px;line-height:7px}
.search svg{position:absolute;right:3px;top:1px}

/* header */
.site-header{left:0;top:11px;width:755px;height:106px;background:var(--header-bg)}
.brand{left:97px;top:31px;display:flex;align-items:center;gap:6px}
.brand-mark{width:14px;height:14px;background:var(--blue)}
.brand-name{font-size:12px;font-weight:600;color:#3e8fc4;line-height:1.05}
.practitioner{left:349px;top:33px;color:#555}
.practitioner .name{font-size:16px;letter-spacing:.3px}
.practitioner .cred{font-size:9px}
.practitioner .role{font-size:8.5px;color:#666;letter-spacing:.3px}
.header-contact{left:97px;top:84px;font-size:10.5px;color:#555;line-height:15px;white-space:nowrap}
.header-contact svg{vertical-align:-1px;margin-right:4px}
.main-nav{left:202px;top:92px;display:flex}
.main-nav a{display:block;height:25px;line-height:27px;text-align:center;background:var(--tab);color:var(--tab-text);font-size:9px;text-decoration:none;border-radius:6px 12px 0 0;letter-spacing:.2px;margin-right:-1px;border-left:1px solid #d6e8f3}

/* hero */
.hero{left:0;top:117px;width:755px;height:309px;background:radial-gradient(circle at 30% 45%,#b79a84 0%,#a99b95 35%,#c9c3c7 70%,#dcd8db 100%)}
.hero-caption{left:388px;top:153px;width:269px;height:40px;background:rgba(150,135,125,.78);color:var(--white);font-size:14px;line-height:40px;padding-left:32px}
.social-rail{left:732px;top:198px;width:23px;height:102px;background:#6e6e6e;border-radius:3px 0 0 3px;padding:4px 3px}
.social-rail span{display:block;width:16px;height:13px;background:#9a9a9a;margin-bottom:3px}

/* section headings */
.section-title{font-family:"Oswald",Arial Narrow,sans-serif;font-weight:500;font-size:11px;letter-spacing:.3px;color:var(--blue);text-transform:uppercase;display:flex;align-items:center;gap:8px;white-space:nowrap}
.section-title .accent{color:var(--orange-text)}
.section-title .dark{color:#2b2b2b}
.section-title::after{content:"";flex:1;height:9px;background:var(--blue-band)}

.photo{box-shadow:1px 2px 3px rgba(0,0,0,.3)}

/* focus areas */
.focus{width:179px}
.focus .photo{position:absolute;top:17px;left:0;width:179px;height:111px}

/* about */
.about-title{left:97px;top:604px;width:370px}
.uni-badge{display:flex;align-items:center;gap:3px;font-size:6px;font-weight:600;color:#2b2b2b;line-height:1}
.uni-badge i{display:block;width:8px;height:8px;border-radius:50%;background:#2b2b2b}
.about-photo{left:97px;top:630px;width:179px;height:116px;background:linear-gradient(100deg,#c9b7a4 0%,#e8e2dc 45%,#8c8f9c 100%)}
.about-text{left:288px;top:628px;width:168px;color:var(--ink-soft);font-size:7.6px;line-height:10.4px}
.about-text p+p{margin-top:4px}
.btn{left:288px;top:738px;width:111px;height:13px;background:var(--orange);color:var(--white);font-family:"Oswald",sans-serif;font-size:8px;text-align:center;line-height:13px;letter-spacing:.3px}

/* research */
.research{left:479px;top:604px;width:178px}
.research ul{list-style:none;margin-top:12px}
.research li{color:#555;font-size:7.6px;line-height:11px;margin-bottom:9px}
.research .meta{color:#666;margin-bottom:3px;display:flex;align-items:center;gap:3px}
.research .meta svg{flex:none}

/* professional development */
.pd-title{left:97px;top:772px;width:560px}
.pd-col{top:802px;width:135px}
.pd-col h3{font-family:"Oswald",sans-serif;font-weight:500;font-size:10px;color:var(--orange-text);letter-spacing:.3px;line-height:13px;text-transform:uppercase}
.pd-col h3.blue{color:var(--blue)}
.pd-col .photo{position:absolute;top:35px;left:2px;width:129px;height:118px}
.bullets{list-style:none;margin-top:7px}
.bullets li{position:relative;padding-left:8px;color:#666;font-size:7.5px;line-height:8.8px;margin-bottom:6px;white-space:nowrap}
.bullets li::before{content:"";position:absolute;left:0;top:2.5px;width:4px;height:4px;border-radius:50%;background:#e86a55}
.bullets small{display:block;font-size:7.3px;color:#777}
.more{position:absolute;left:107px;top:146px;font-size:7.5px;color:var(--orange-text)}
.divider{left:370px;top:835px;width:1px;height:122px;background:var(--peach)}

/* partners */
.partners-title{left:97px;top:993px;width:560px}
.partners{left:102px;top:1022px;width:552px;display:flex;justify-content:space-between;align-items:center}
.partners span{display:block;height:22px;background:#e1e4e7;border-radius:2px}

/* footer */
.site-footer{left:0;top:1071px;width:755px;height:109px;background:var(--teal)}
.footer-brands{left:97px;top:1090px;display:flex;align-items:center;gap:12px}
.footer-brands .uni-badge{font-size:6.5px;flex-direction:column;align-items:flex-start;gap:2px}
.footer-address{left:329px;top:1090px;font-size:8.5px;line-height:10.5px;color:#333}
.footer-contact{left:526px;top:1090px;font-size:8.5px;color:#333;line-height:15px}
.footer-contact h4{font-family:"Oswald",sans-serif;font-weight:500;font-size:10px;color:#333;letter-spacing:.3px;margin-bottom:3px}
.footer-contact svg{vertical-align:-1px;margin-right:5px}
.bottom-bar{left:0;top:1180px;width:755px;height:20px;background:var(--orange);font-size:7px;color:#5a3a2a;line-height:20px}
.bottom-bar .copy{position:absolute;left:97px}
.bottom-bar nav{position:absolute;left:226px;display:flex;gap:14px}
.bottom-bar .back{position:absolute;left:619px}
</style>
</head>
<body>

<div class="abs top-strip"></div>
<div class="abs search">Search...
  <svg width="6" height="6" viewBox="0 0 6 6"><circle cx="2.5" cy="2.5" r="1.8" fill="none" stroke="#666" stroke-width=".8"/><line x1="3.8" y1="3.8" x2="5.6" y2="5.6" stroke="#666" stroke-width=".8"/></svg>
</div>

<header class="abs site-header"></header>
<div class="abs brand">
  <span class="brand-mark"></span>
  <div class="brand-name">Larkhollow<br>Consultants</div>
</div>
<div class="abs practitioner">
  <div><span class="name">Dr.XYZ</span> <span class="cred">Ph.D. CCC-SLP</span></div>
  <div class="role">Speech-Language Pathologist</div>
</div>
<div class="abs header-contact">
  <div><svg width="9" height="7" viewBox="0 0 9 7"><rect x=".5" y=".5" width="8" height="6" fill="#666"/><path d="M.5 .5 4.5 4 8.5 .5" fill="none" stroke="#ededed" stroke-width=".8"/></svg>info@lhc.com</div>
  <div><svg width="9" height="9" viewBox="0 0 6 9"><path d="M1.5 .5 Q.3 4.5 1.5 8.5 L3 8 2.4 6 Q1.7 4.5 2.4 3 L3 1z" fill="#666"/></svg>+312 555 0147</div>
</div>
<nav class="abs main-nav">
  <a href="#" style="width:63px">HOME</a><a href="#" style="width:91px">CONSULTATION</a><a href="#" style="width:70px">RESEARCH</a><a href="#" style="width:152px">PROFESSIONAL DEVELOPMENT</a><a href="#" style="width:74px">CONTACT</a>
</nav>

<section class="abs hero" role="img" aria-label="Young boy using a tablet computer at a table"></section>
<div class="abs hero-caption">Mobile Technology for Autism</div>
<div class="abs social-rail" aria-label="Social links">
  <span></span><span></span><span></span><span></span><span></span><span></span>
</div>

<section class="abs focus" style="left:97px;top:447px">
  <h2 class="section-title">Assistive Technology</h2>
  <div class="photo" role="img" aria-label="Toddler tapping picture cards on a tablet" style="background:linear-gradient(120deg,#7a2f2f,#b88b7a 50%,#d9d2cc)"></div>
</section>
<section class="abs focus" style="left:288px;top:447px">
  <h2 class="section-title">Early Language Learning</h2>
  <div class="photo" role="img" aria-label="Newborn baby lying on a white blanket" style="background:linear-gradient(120deg,#eee7e0,#d9bfae 50%,#f2eeea)"></div>
</section>
<section class="abs focus" style="left:479px;top:447px">
  <h2 class="section-title">Reading Difficulties</h2>
  <div class="photo" role="img" aria-label="Boy frustrated over an open book" style="background:linear-gradient(120deg,#6c9a3e,#b7c98a 45%,#c9a27c)"></div>
</section>

<div class="abs about-title">
  <h2 class="section-title"><span class="uni-badge"><i></i>Ashgrove State</span><span><span class="accent">About</span> <span class="dark">Dr. XYZ</span></span></h2>
</div>
<div class="abs about-photo photo" role="img" aria-label="Clinician in a white coat with an infant"></div>
<div class="abs about-text">
  <p>"...We provide the best evidence-based services/interventions, at an affordable fee, and deal only with clients who seek such services...."</p>
  <p>Temporibus autem quibusdam et aut officiis debitis aut rerum necessitatibus saepe eveniet ut et voluptates repudiandae sint et molestiae non recusandae.Itaque earum rerum hic tenetur a sapiente delectus.</p>
</div>
<a class="abs btn">WHAT MAKES US DIFFERENT</a>

<section class="abs research">
  <h2 class="section-title"><span>Research <span class="accent">Updates 365</span></span></h2>
  <ul>
    <li><div class="meta"><svg width="8" height="8" viewBox="0 0 8 8"><circle cx="4" cy="4" r="3.3" fill="none" stroke="#888"/><path d="M4 2v2h1.6" fill="none" stroke="#888" stroke-width=".8"/></svg>17 Jun 2014 <svg width="9" height="7" viewBox="0 0 9 7"><ellipse cx="4.5" cy="3" rx="4.2" ry="2.8" fill="#888"/><path d="M2 5 1 7 4 5.5z" fill="#888"/></svg>100 comments</div>Autism symptoms ‘reversed’ in mice by<br>100-year-old drug.</li>
    <li><div class="meta"><svg width="8" height="8" viewBox="0 0 8 8"><circle cx="4" cy="4" r="3.3" fill="none" stroke="#888"/><path d="M4 2v2h1.6" fill="none" stroke="#888" stroke-width=".8"/></svg>20 Jun 2014 <svg width="9" height="7" viewBox="0 0 9 7"><ellipse cx="4.5" cy="3" rx="4.2" ry="2.8" fill="#888"/><path d="M2 5 1 7 4 5.5z" fill="#888"/></svg>80 comments</div>Autism link discovered in brains of mice<br>with ‘mohawks’.</li>
    <li><div class="meta"><svg width="8" height="8" viewBox="0 0 8 8"><circle cx="4" cy="4" r="3.3" fill="none" stroke="#888"/><path d="M4 2v2h1.6" fill="none" stroke="#888" stroke-width=".8"/></svg>20 Jun 2014 <svg width="9" height="7" viewBox="0 0 9 7"><ellipse cx="4.5" cy="3" rx="4.2" ry="2.8" fill="#888"/><path d="M2 5 1 7 4 5.5z" fill="#888"/></svg>80 comments</div>Children with autism have mitochondrial<br>deficits.</li>
  </ul>
</section>

<div class="abs pd-title"><h2 class="section-title"><span><span class="accent">Professional</span> Development</span></h2></div>

<section class="abs pd-col" style="left:97px">
  <h3>Seminars</h3>
  <div class="photo" role="img" aria-label="Audience raising hands at a seminar" style="background:linear-gradient(130deg,#6d7fa3,#b8aaa6 55%,#d8cfc6)"></div>
</section>
<section class="abs pd-col" style="left:240px">
  <h3 class="blue">Upcoming Seminars<br>Activities</h3>
  <ul class="bullets">
    <li>Key Word Signing for children<br>with communication.<br>– 4 – 5 hours.</li>
    <li>Children’s Speech and<br>Language Development.<br>– 1 hour.</li>
    <li>Phonological Awareness:<br>The Building Blocks .<br>Success – 2 hours.</li>
    <li>Phonological Awareness:<br>The Building Blocks .<br>Success – 2 hours.</li>
  </ul>
  <span class="more">more</span>
</section>
<div class="abs divider"></div>
<section class="abs pd-col" style="left:383px">
  <h3>E-Learning</h3>
  <div class="photo" role="img" aria-label="Businessman holding a tablet showing an e-learning screen" style="background:linear-gradient(180deg,#f2f2f2,#8a8a8a 45%,#4a4a4a)"></div>
</section>
<section class="abs pd-col" style="left:526px">
  <h3 class="blue">Recent Courses</h3>
  <ul class="bullets">
    <li>Speech and Language Therapy<br>MSc.<small>Temporibus autem quibusdam et<br>aut officiis debitis aut rerum .</small></li>
    <li>Speech and Language Therapy<br>PgDip.<small>Temporibus autem quibusdam et<br>aut officiis debitis aut rerum .</small></li>
    <li>Speech and Language Sciences<br>MSc.<small>Temporibus autem quibusdam et<br>aut officiis debitis aut rerum .</small></li>
  </ul>
</section>

<div class="abs partners-title"><h2 class="section-title">Our Partners</h2></div>
<div class="abs partners" aria-label="Partner organisations">
  <span style="width:80px"></span><span style="width:42px"></span><span style="width:34px"></span><span style="width:36px"></span><span style="width:66px"></span><span style="width:72px"></span><span style="width:80px"></span>
</div>

<footer class="abs site-footer"></footer>
<div class="abs footer-brands">
  <div class="uni-badge"><i></i>Ashgrove State<br>University</div>
  <div class="brand-name" style="font-size:10px;display:flex;align-items:center;gap:5px"><span class="brand-mark" style="width:12px;height:12px"></span>Larkhollow<br>Consultants</div>
</div>
<div class="abs footer-address">
  Dr. XYZ, Ph.D.<br>Associate Professor<br>Department of ABC<br>College of yadi yadi yada
</div>
<div class="abs footer-contact">
  <h4><svg width="9" height="7" viewBox="0 0 9 7"><rect x=".5" y=".5" width="8" height="6" fill="#333"/><path d="M.5 .5 4.5 4 8.5 .5" fill="none" stroke="#b7dad6" stroke-width=".8"/></svg>CONTACT US</h4>
  <div><svg width="9" height="7" viewBox="0 0 9 7"><rect x=".5" y=".5" width="8" height="6" fill="#333"/><path d="M.5 .5 4.5 4 8.5 .5" fill="none" stroke="#b7dad6" stroke-width=".8"/></svg>info@lhc.com</div>
  <div><svg width="9" height="8" viewBox="0 0 9 8"><path d="M1 1.5 Q1 6.5 7 7 L8 5.5 6 4.5 5 5.5 Q3 4.5 2.5 3 L3.5 2 2.5 0z" fill="#333"/></svg>+312 555 0147</div>
</div>
<div class="abs bottom-bar">
  <span class="copy">copyright information here</span>
  <nav><span>Home</span><span>Consultation</span><span>Research</span><span>Site Map</span></nav>
  <span class="back">Back to top</span>
</div>

</body>
</html>
```